Birchline Septic Solutions

Would like to see some single sided ones but would also like to see some double sided with one sided only being the logo. Owners name is Colin Vandro. Phone number is 555-214-0387
Services are pumping, inspections, installs, and repairs

Contact Information for Business Card

555-241-0387 Colin Vandro Fairhaven, OH

```html
<!DOCTYPE html>
<html lang="en">
<head>
<meta charset="utf-8">
<title>Birchline Septic Solutions – Business Card</title>
<link href="https://fonts.googleapis.com/css2?family=Open+Sans:wght@400;600;700&display=swap" rel="stylesheet">
<style>
  :root {
    --stage: #232323;
    --card-dark: #1e1f22;
    --teal: #25bfb9;
    --teal-deep: #1a9d98;
    --white: #ffffff;
    --muted: #e6e6e6;
    --art-top: rgba(58, 59, 62, 0);
    --art-bottom: #2e2f33;
  }
  * { box-sizing: border-box; margin: 0; padding: 0; }
  html, body {
    width: 1200px; height: 779px; overflow: hidden;
    background: var(--stage);
    font-family: "Open Sans", sans-serif;
  }
  .stage {
    width: 1200px; height: 779px;
    display: flex; align-items: center; justify-content: center; gap: 30px;
  }
  .card {
    position: relative; width: 560px; height: 320px; overflow: hidden;
    box-shadow: 0 18px 40px rgba(0, 0, 0, .45);
  }

  /* Front */
  .card-front { background: var(--card-dark); color: var(--white); }
  .brand-name {
    position: absolute; left: 150px; top: 36px; width: 300px;
    font-weight: 700; font-size: 30px; line-height: 1.1;
    color: var(--white);
  }
  .services { position: absolute; left: 34px; top: 132px; z-index: 1; }
  .services-title {
    color: var(--teal); font-weight: 600; font-size: 14px;
    text-transform: uppercase; margin-bottom: 2px;
  }
  .services-list { list-style: none; }
  .services-list li {
    font-size: 14px; line-height: 19px; color: var(--muted);
    display: flex; align-items: center; gap: 8px;
  }
  .services-list li::before {
    content: ""; width: 8px; height: 8px; border-radius: 50%; background: var(--teal);
  }
  .landscape-art {
    position: absolute; left: 150px; right: 0; bottom: 0; height: 72px;
    background: linear-gradient(180deg, var(--art-top), var(--art-bottom));
  }
  .contact {
    position: absolute; right: 44px; top: 148px; text-align: right; z-index: 1;
  }
  .contact-name { font-size: 26px; font-weight: 700; line-height: 1.15; }
  .contact-name .first { color: var(--teal); }
  .contact-name .last { color: var(--white); }
  .contact-line { font-size: 14px; color: var(--muted); line-height: 21px; }
  .contact-phone { display: inline-flex; align-items: center; gap: 6px; }
  .contact-phone svg { width: 13px; height: 13px; }
  .accent-strip {
    position: absolute; right: 0; top: 150px; width: 26px; height: 88px;
    background: var(--teal);
  }

  /* Back */
  .card-back {
    background: var(--teal);
    display: flex; align-items: center; justify-content: center;
  }
  .brand-name-back {
    font-weight: 700; font-size: 34px; color: var(--teal-deep);
    text-align: center; line-height: 1.15; width: 360px;
  }
</style>
</head>
<body>
<main class="stage">
  <section class="card card-front" aria-label="Business card front">
    <p class="brand-name">Birchline Septic Solutions</p>

    <div class="services">
      <p class="services-title">Services</p>
      <ul class="services-list">
        <li>Pumping</li>
        <li>Inspections</li>
        <li>Installs</li>
        <li>And Repairs</li>
      </ul>
    </div>

    <div class="landscape-art" role="img" aria-label="Subtle dark landscape artwork along the bottom of the card"></div>

    <div class="contact">
      <p class="contact-name"><span class="first">Colin</span> <span class="last">Vandro</span></p>
      <p class="contact-line">Fairhaven, OH</p>
      <p class="contact-line contact-phone">555-241-0387
        <svg viewBox="0 0 24 24" aria-hidden="true"><path fill="#25bfb9" d="M6.6 10.8a15 15 0 0 0 6.6 6.6l2.2-2.2a1 1 0 0 1 1-.25 11.4 11.4 0 0 0 3.6.57 1 1 0 0 1 1 1V20a1 1 0 0 1-1 1A17 17 0 0 1 3 4a1 1 0 0 1 1-1h3.5a1 1 0 0 1 1 1c0 1.25.2 2.45.57 3.57a1 1 0 0 1-.25 1z"/></svg>
      </p>
    </div>
    <div class="accent-strip"></div>
  </section>

  <section class="card card-back" aria-label="Business card back">
    <p class="brand-name-back">Birchline Septic Solutions</p>
  </section>
</main>
</body>
</html>
```